Business card design for new eCommerce site focusing on integrity and strong businsess tactics

We need a business card that will stand out and be memorable. Something with color that matches our company logo colors. Think high end version of Pactivo. There are 2 logos provided. The parent company is called Amber Ledge Partners and we are presenting a new and very exciting eCommerce site called BrightHarborTrade.example.

Target Market(s)

Our target markets are in the Activities, Food and Beverage, Health and Beauty

Industry/Entity Type

Marketing

Contact Information for Business Card

We have 4 members that need cards...I will provide all info to the winner of the design contest
Business Address is
4870 West 63rd Avenue, Suite C207
Phoenix AZ 85731

Font styles to use
Serif
Sans Serif

Colors

Designer to choose colors to be used in the design.

Requirements
Must have
• The card must be memorable...should be unique in design but must exude integrity and be playful .
• I have provided several colors or our parent company...please feel free to use which ever
Nice to have
• I will leave this up to you. Feel free to use other images of your choosing that wraps around our client.....Activities, Dining, Health, Beauty
Should not have
• just dont be boring

```html
<!DOCTYPE html>
<html lang="en">
<head>
<meta charset="utf-8">
<title>Amber Ledge Partners – Business Card</title>
<link href="https://fonts.googleapis.com/css2?family=Open+Sans:wght@400;600;700&display=swap" rel="stylesheet">
<style>
  :root {
    --navy: #111d46;
    --paper: #f4f4f4;
    --stage: #d4d4d4;
    --ink: #1f1f25;
    --white: #ffffff;
  }
  * { box-sizing: border-box; margin: 0; padding: 0; }
  html, body {
    width: 1200px; height: 904px; overflow: hidden;
    background: var(--stage);
    font-family: "Open Sans", Arial, sans-serif;
  }
  .canvas {
    position: relative; width: 1200px; height: 904px;
    display: flex; flex-direction: column; align-items: center; justify-content: center; gap: 44px;
  }
  .card {
    position: relative; width: 620px; height: 354px;
    box-shadow: 0 6px 18px rgba(0,0,0,.18);
    overflow: hidden;
  }
  /* Front */
  .card--front { background: var(--navy); }
  .brand {
    position: absolute; left: 0; right: 0; top: 157px;
    display: flex; align-items: center; justify-content: center; gap: 14px; color: var(--white);
  }
  .brand__dot { width: 40px; height: 40px; border-radius: 50%; background: var(--white); flex: none; }
  .brand__name { font-size: 26px; font-weight: 700; letter-spacing: -0.3px; line-height: 1; }
  /* Back */
  .card--back { background: linear-gradient(160deg, #ffffff 0%, var(--paper) 60%, #e9e9e9 100%); }
  .band {
    position: absolute; left: 95px; right: 0; top: 38px; height: 96px;
    background: var(--navy);
  }
  .holder {
    position: absolute; right: 30px; top: 50px; text-align: right; color: var(--white);
  }
  .holder__name { font-size: 20px; font-weight: 700; line-height: 1.1; }
  .holder__title { font-size: 12px; font-weight: 400; margin-top: 2px; }
  .seal {
    position: absolute; left: 32px; top: 72px; width: 126px; height: 126px;
    border-radius: 50%; background: var(--navy); border: 7px solid var(--white);
    box-shadow: 0 0 0 2px var(--navy);
  }
  .company {
    position: absolute; left: 34px; top: 206px;
    font-size: 29px; font-weight: 700; color: var(--navy); letter-spacing: -0.5px;
  }
  .address {
    position: absolute; left: 36px; top: 268px;
    font-size: 15px; line-height: 1.35; color: var(--ink); font-style: normal;
  }
  .divider {
    position: absolute; left: 318px; top: 262px; width: 1px; height: 66px; background: var(--ink);
  }
  .contacts {
    position: absolute; left: 332px; top: 260px; list-style: none;
    font-size: 14.5px; color: var(--ink);
  }
  .contacts li { display: flex; align-items: center; gap: 9px; height: 23px; }
  .contacts svg { width: 14px; height: 14px; flex: none; }
</style>
</head>
<body>
<main class="canvas">
  <section class="card card--front" aria-label="Card front">
    <div class="brand">
      <span class="brand__dot"></span>
      <div class="brand__name">BrightHarborTrade.example</div>
    </div>
  </section>

  <section class="card card--back" aria-label="Card back">
    <div class="band"></div>
    <div class="holder">
      <div class="holder__name">Dana Whitfield</div>
      <div class="holder__title">Manager</div>
    </div>
    <div class="seal"></div>
    <div class="company">Amber Ledge Partners</div>
    <address class="address">
      4870 West 63rd Avenue<br>Suite C207<br>Phoenix AZ 85731
    </address>
    <div class="divider"></div>
    <ul class="contacts">
      <li>
        <svg viewBox="0 0 16 16" aria-hidden="true"><circle cx="8" cy="8" r="8" fill="var(--navy)"/><path d="M5 4.5c.6-.4 1.1-.2 1.4.4l.5 1c.2.4 0 .8-.3 1l-.4.3c.4 1 1.1 1.7 2.1 2.1l.3-.4c.2-.3.6-.5 1-.3l1 .5c.6.3.8.8.4 1.4-.5.8-1.4 1-2.3.6A7 7 0 0 1 4.4 6.8C4 5.9 4.2 5 5 4.5Z" fill="#fff"/></svg>
        +999 9999 9999
      </li>
      <li>
        <svg viewBox="0 0 16 16" aria-hidden="true"><circle cx="8" cy="8" r="8" fill="var(--navy)"/><rect x="4" y="5" width="8" height="6" rx="0.8" fill="#fff"/><path d="M4.3 5.4 8 8.4l3.7-3" stroke="var(--navy)" stroke-width="1" fill="none"/></svg>
        info@amberledge.example
      </li>
      <li>
        <svg viewBox="0 0 16 16" aria-hidden="true"><circle cx="8" cy="8" r="8" fill="var(--navy)"/><circle cx="8" cy="8" r="4.2" fill="none" stroke="#fff" stroke-width="1"/><path d="M3.8 8h8.4M8 3.8c-2 2.4-2 6 0 8.4M8 3.8c2 2.4 2 6 0 8.4" stroke="#fff" stroke-width="0.9" fill="none"/></svg>
        www.amberledge.example
      </li>
    </ul>
  </section>
</main>
</body>
</html>
```